New Business Card Design Project

We require a business card design for Vexalund, a newly established Indian company.
Our focus is on the development, manufacturing, and export of a diverse array of pharmaceutical products on a global scale. The card should convey a professional appearance, as our primary markets are in Africa, China, and Southeast Asian nations.
We envision a two-sided business card, with the reverse side dedicated to a logo set against a solid color or an elegantly designed pattern. The corners should be rounded. We would appreciate seeing both horizontal and vertical design options. We trust the designer to utilize their expertise in creating this design.

The content for the business card is included in the attached Word file.

Target Market(s)

Our primary markets are in Africa, China, and Southeast Asian, Latin America, Maldives, Sri Lanka

Industry/Entity Type

Pharmaceutical Manufacturing and Export

Contact Information for Business Card

Colors

Designer to choose colors to be used in the design.

Requirements
Must have
• The reverse side of the business card features solely the logo along with the tagline, "Care for Every Day."
Should not have
• The logo should not exceed two instances, encompassing both the front and back sides of the card.

```html
<!DOCTYPE html>
<html lang="en">
<head>
<meta charset="utf-8">
<title>Vexalund Business Card</title>
<link href="https://fonts.googleapis.com/css2?family=Quicksand:wght@700&family=Open+Sans:wght@400;600&display=swap" rel="stylesheet">
<style>
  :root {
    --backdrop: #232325;
    --card-dark: #222326;
    --coral: #e15b4a;
    --coral-bright: #ef5d4a;
    --blue: #2aa7e0;
    --cream: #ece9e4;
    --ink-light: #f1f1f1;
  }
  * { box-sizing: border-box; margin: 0; padding: 0; }
  html, body {
    width: 1200px; height: 780px; overflow: hidden;
    background: var(--backdrop);
  }
  .stage {
    position: relative; width: 1200px; height: 780px;
    display: flex; align-items: center; justify-content: center; gap: 40px;
  }
  .card {
    position: relative; width: 540px; height: 310px;
    border-radius: 22px; overflow: hidden;
    box-shadow: 0 12px 30px rgba(0,0,0,.45);
  }

  /* Front */
  .card--front { background: var(--card-dark); font-family: "Open Sans", sans-serif; }
  .brand {
    position: absolute; left: 30px; top: 64px;
    display: flex; align-items: center; gap: 10px;
  }
  .brand__dot { width: 20px; height: 20px; border-radius: 50%; background: var(--coral-bright); }
  .brand__name {
    font-family: "Quicksand", sans-serif; font-weight: 700;
    font-size: 38px; line-height: 1; color: var(--blue);
  }
  .divider {
    position: absolute; left: 282px; top: 40px; width: 1px; height: 180px;
    background: linear-gradient(to bottom, transparent, var(--coral) 30%, var(--coral) 70%, transparent);
  }
  .person { position: absolute; left: 306px; top: 62px; }
  .person__name {
    font-family: "Quicksand", sans-serif; font-weight: 700; font-size: 24px;
    color: var(--coral-bright); white-space: nowrap;
  }
  .person__first { color: var(--blue); }
  .person__role { font-size: 13px; color: var(--ink-light); margin-top: 2px; }
  .contacts { position: absolute; left: 306px; top: 138px; list-style: none; }
  .contacts li {
    display: flex; align-items: center; gap: 10px;
    font-size: 13.5px; color: var(--ink-light); line-height: 26px; white-space: nowrap;
  }
  .contacts svg { width: 14px; height: 14px; flex: none; }
  .band {
    position: absolute; left: 0; bottom: 26px; height: 30px;
    display: flex; align-items: center;
  }
  .band__address {
    width: 380px; height: 30px; background: var(--blue);
    color: #fff; font-size: 12.5px; line-height: 30px; padding-left: 34px; white-space: nowrap;
  }
  .band__mark {
    width: 70px; height: 30px; display: flex; align-items: center; justify-content: center;
    font-family: "Quicksand", sans-serif; font-weight: 700; font-size: 11px; color: var(--blue);
  }
  .band__tail { width: 90px; height: 30px; background: var(--coral-bright); }

  /* Back */
  .card--back { background: var(--coral); }
  .back-group {
    position: absolute; left: 50%; top: 110px; transform: translateX(-50%);
    display: flex; flex-direction: column; align-items: flex-start; gap: 14px;
  }
  .back-brand { display: flex; align-items: center; gap: 14px; }
  .back-brand__dot { width: 26px; height: 26px; border-radius: 50%; background: var(--cream); }
  .back-brand__name {
    font-family: "Quicksand", sans-serif; font-weight: 700; font-size: 56px; line-height: 1; color: var(--cream);
  }
  .tagline {
    font-family: "Open Sans", sans-serif; font-size: 13px; color: var(--cream); letter-spacing: .4px;
  }
</style>
</head>
<body>
<main class="stage">
  <section class="card card--front" aria-label="Business card front">
    <div class="brand">
      <span class="brand__dot"></span>
      <span class="brand__name">Vexalund</span>
    </div>
    <div class="divider"></div>
    <div class="person">
      <p class="person__name"><span class="person__first">Rohan</span> K. Desai</p>
      <p class="person__role">CEO</p>
    </div>
    <ul class="contacts">
      <li>
        <svg viewBox="0 0 14 14"><rect x="3" y="1" width="8" height="12" rx="1.5" fill="none" stroke="var(--coral-bright)" stroke-width="1.4"/></svg>
        +91 98765 43210
      </li>
      <li>
        <svg viewBox="0 0 14 14"><circle cx="7" cy="7" r="6" fill="var(--blue)"/><path d="M1 7h12M7 1c2.5 3 2.5 9 0 12M7 1c-2.5 3-2.5 9 0 12" stroke="#fff" stroke-width=".8" fill="none"/></svg>
        www.vexalund.com
      </li>
      <li>
        <svg viewBox="0 0 14 14"><rect x="1" y="3" width="12" height="9" rx="1" fill="var(--coral-bright)"/><path d="M1 3l6 5 6-5" stroke="#fff" stroke-width="1" fill="none"/></svg>
        rdesai@vexalund.com
      </li>
    </ul>
    <div class="band">
      <div class="band__address">12, Lotus Nagar, Nashik, 422001, India</div>
      <div class="band__mark">Vexalund</div>
      <div class="band__tail"></div>
    </div>
  </section>

  <section class="card card--back" aria-label="Business card back">
    <div class="back-group">
      <div class="back-brand">
        <span class="back-brand__dot"></span>
        <span class="back-brand__name">Vexalund</span>
      </div>
      <p class="tagline">Care for Every Day.</p>
    </div>
  </section>
</main>
</body>
</html>
```